BRELWINCare.co.uk - Mental Health Clinic for Child and Adolescents

Updated 29/01/2018***
I am not sure you guys are getting the idea regards to the opening page / homescreen layout. Can you look at the new images I have uploaded (page 5, 6 and 7) These are some of the layouts I like but to incorporate my chosen images, with the BRELWIN commissioner, buttons and a sliding header bar.
I have written a strong brief, I am looking for a website, preferably wordpress as i know they are easy to maintain. I am looking for a one page site, with the top / opening page being full screen image with drop down categories. I have made a rough design, see full brief in word doc attached, there is some freedom to play around with the design aspect but it will need to relay all the content provided. I like a minimal feel. I have also attached some images that may be useful, but will need a new logo for BRELWIN Care. I have attached some logo idea's, it is up to you decide whether you want to use them.
I would prefer the homepage as full screen image, and the categories offered as a drop down or over the main image.
I have also attached linked to some competitors websites:
https://www.vorimant-health.co.uk/
http://www.qlbn.org.uk/
Industry/Entity Type
Clinic
Number of Pages Required
1 page
Font styles to use
Look and feel
Each slider illustrates characteristics of the customer's brand and the style your logo design should communicate.

```html
<!DOCTYPE html>
<html lang="en">
<head>
<meta charset="utf-8">
<title>BRELWIN Care – Child &amp; Adolescent Mental Health Services</title>
<link rel="stylesheet" href="https://fonts.googleapis.com/css2?family=Poppins:wght@300;400&family=Open+Sans:wght@400&display=swap">
<style>
  :root {
    --pink: #e6007e;
    --pink-soft: #f7c6e2;
    --cyan: #17b6cf;
    --black: #000;
    --ink: #222;
    --muted: #555;
    --rule: #3a3a3a;
    --gold: #c9b24a;
    --white: #fff;
  }
  * { box-sizing: border-box; margin: 0; padding: 0; }
  html, body { width: 849px; height: 1200px; overflow: hidden; background: var(--white); }
  body { position: relative; font-family: "Poppins", sans-serif; color: var(--ink); }

  .sidebar { position: absolute; left: 0; top: 0; width: 171px; height: 506px; background: var(--black); }
  .brand { position: absolute; left: 19px; top: 30px; display: flex; align-items: center; gap: 7px; }
  .brand-mark { width: 30px; height: 30px; border-radius: 50%; background: #f2e600; flex: none; }
  .brand-name { color: var(--white); font-weight: 400; font-size: 15px; line-height: 1; letter-spacing: .5px; }
  .brand-tag { color: var(--white); font-weight: 300; font-size: 6px; line-height: 1.3; margin-top: 3px; }
  .main-nav { position: absolute; left: 22px; top: 128px; width: 131px; list-style: none; }
  .main-nav li { height: 31.2px; display: flex; align-items: center; padding-left: 7px;
    border-bottom: 1px solid var(--rule); color: var(--white); font-size: 9.6px; font-weight: 400; letter-spacing: .1px; }
  .main-nav li.current { border-bottom-color: var(--gold); }
  .main-nav li:last-child { border-bottom: none; }

  .hero { position: absolute; left: 171px; top: 0; width: 678px; height: 417px;
    background: linear-gradient(120deg, #e9e4df 0%, #d9d2ca 35%, #b9a999 60%, #ece8e3 100%); }
  .hero-btn { position: absolute; top: 314px; height: 41px; display: flex; align-items: center; justify-content: center;
    color: var(--white); font-size: 17.6px; font-weight: 400; letter-spacing: .3px; }
  .hero-btn.parents { left: 163px; width: 131px; background: var(--cyan); }
  .hero-btn.commissioners { left: 328px; width: 193px; background: var(--pink); }

  .slide-bar { position: absolute; left: 171px; top: 417px; width: 678px; height: 89px; background: var(--pink); }
  .slide-bar h2 { position: absolute; left: 35px; top: 26px; color: var(--white); font-weight: 400; font-size: 24px; letter-spacing: .2px; }
  .slide-arrows { position: absolute; left: 572px; top: 24px; display: flex; }
  .slide-arrows span { width: 41.5px; height: 41px; display: flex; align-items: center; justify-content: center; }
  .slide-arrows .prev { background: var(--pink-soft); }
  .slide-arrows .next { background: var(--white); }

  .section-title { position: absolute; left: 193px; font-size: 17.6px; font-weight: 400; color: var(--ink); letter-spacing: .2px; }
  .blog-title { top: 550px; }
  .post { position: absolute; top: 590px; width: 194px; }
  .post-1 { left: 193px; } .post-2 { left: 413px; } .post-3 { left: 633px; }
  .post-photo { height: 148px; }
  .post-1 .post-photo { background: linear-gradient(135deg, #8fa7c3, #d8d2c8 60%, #b6a89a); }
  .post-2 .post-photo { background: linear-gradient(135deg, #c9a58d, #efe6dd 55%, #b48268); }
  .post-3 .post-photo { background: linear-gradient(135deg, #e6e3df, #9e8f7f 55%, #5c6f74); }
  .post-date { margin-top: 10px; font-size: 8.6px; color: var(--muted); font-weight: 300; }
  .post h3 { margin-top: 7px; font-size: 12.6px; font-weight: 400; color: #333; }
  .post p { margin-top: 8px; font-size: 8.6px; line-height: 15.5px; color: var(--muted); font-weight: 300; }
  .read-more { display: flex; align-items: center; gap: 2px; margin-top: 17px; font-size: 8.6px; }
  .post-1 .read-more, .post-3 .read-more { color: var(--cyan); }
  .post-2 .read-more { color: var(--pink); }

  .contact-title { top: 915px; }
  .contact-list { position: absolute; left: 198px; top: 961px; list-style: none; font-family: "Open Sans", sans-serif; font-size: 9.2px; color: #111; }
  .contact-list li { position: absolute; left: 0; display: flex; align-items: flex-start; gap: 14px; white-space: nowrap; }
  .contact-list svg { flex: none; margin-top: 1px; }
  .contact-list .name { font-family: "Poppins", sans-serif; font-size: 12px; letter-spacing: .3px; display: block; margin-bottom: 1px; }
  .social { position: absolute; top: 1094px; left: 198px; display: flex; gap: 9px; }
  .social span { width: 22px; height: 22px; border-radius: 50%; }

  .map { position: absolute; left: 496px; top: 913px; width: 330px; height: 226px; border: 2px solid #f08cc4;
    background: linear-gradient(160deg, #eceef0 0%, #e3e5e8 55%, #f3e8b8 75%, #e6e8ea 100%); }

  .site-footer { position: absolute; left: 0; top: 1166px; width: 849px; height: 34px; background: var(--black); }
  .site-footer p { position: absolute; left: 192px; top: 11px; color: #ddd; font-size: 9px; font-weight: 300; }
</style>
</head>
<body>
  <aside class="sidebar">
    <div class="brand">
      <span class="brand-mark"></span>
      <div>
        <div class="brand-name">BRELWIN</div>
        <div class="brand-tag">Child &amp; Adolescent Mental<br>Health Services</div>
      </div>
    </div>
    <ul class="main-nav">
      <li class="current">HOME</li>
      <li>ABOUT US</li>
      <li>OUR TEAM</li>
      <li>OUR SERVICES</li>
      <li>CONTACT US</li>
      <li>PARENTS</li>
      <li>COMMISSIONERS</li>
      <li>BLOG</li>
      <li>FORUM</li>
    </ul>
  </aside>

  <section class="hero" role="img" aria-label="Photo of a therapist talking with a young boy in a bright living room">
    <span class="hero-btn parents">PARENTS</span>
    <span class="hero-btn commissioners">COMMISSIONERS</span>
  </section>

  <div class="slide-bar">
    <h2>ADHD and autism screening within 24 hours</h2>
    <div class="slide-arrows">
      <span class="prev"><svg width="14" height="20" viewBox="0 0 14 20"><path d="M11 2 L3 10 L11 18" fill="none" stroke="#111" stroke-width="2.2"/></svg></span>
      <span class="next"><svg width="14" height="20" viewBox="0 0 14 20"><path d="M3 2 L11 10 L3 18" fill="none" stroke="#111" stroke-width="2.2"/></svg></span>
    </div>
  </div>

  <h2 class="section-title blog-title">LATEST FROM OUR BLOG</h2>

  <article class="post post-1">
    <div class="post-photo" role="img" aria-label="Photo of a counsellor with a young girl on a sofa"></div>
    <div class="post-date">January 18, 2018</div>
    <h3>The standard Lorem</h3>
    <p>Lorem ipsum dolor sit amet, consectetur adipiscing elit, sed do eiusmod tempor inci-didunt ut labore et dolore magna aliqua.</p>
    <div class="read-more">Read more <svg width="10" height="6" viewBox="0 0 10 6"><path d="M0 3 H8 M6 1 L9 3 L6 5" fill="none" stroke="currentColor" stroke-width="1.2"/></svg></div>
  </article>

  <article class="post post-2">
    <div class="post-photo" role="img" aria-label="Photo of a teacher talking with a girl at a desk"></div>
    <div class="post-date">January 17, 2018</div>
    <h3>The standard Lorem</h3>
    <p>Lorem ipsum dolor sit amet, consectetur adipiscing elit, sed do eiusmod tempor inci-didunt ut labore et dolore magna aliqua.</p>
    <div class="read-more">Read more <svg width="10" height="6" viewBox="0 0 10 6"><path d="M0 3 H8 M6 1 L9 3 L6 5" fill="none" stroke="currentColor" stroke-width="1.2"/></svg></div>
  </article>

  <article class="post post-3">
    <div class="post-photo" role="img" aria-label="Photo of a group of teenagers sitting together on a sofa"></div>
    <div class="post-date">January 16, 2018</div>
    <h3>The standard Lorem</h3>
    <p>Lorem ipsum dolor sit amet, consectetur adipiscing elit, sed do eiusmod tempor inci-didunt ut labore et dolore magna aliqua.</p>
    <div class="read-more">Read more <svg width="10" height="6" viewBox="0 0 10 6"><path d="M0 3 H8 M6 1 L9 3 L6 5" fill="none" stroke="currentColor" stroke-width="1.2"/></svg></div>
  </article>

  <h2 class="section-title contact-title">GET IN TOUCH</h2>

  <ul class="contact-list">
    <li style="top:0">
      <svg width="8" height="10" viewBox="0 0 8 10"><path d="M4 0 A4 4 0 0 1 8 4 C8 6.5 4 10 4 10 C4 10 0 6.5 0 4 A4 4 0 0 1 4 0 Z" fill="#111"/><circle cx="4" cy="4" r="1.5" fill="#fff"/></svg>
      <div><span class="name">BRELWIN CARE</span>Ashcombe Suite 4B, 27-31 Marlow Street, London, E17 9LT.</div>
    </li>
    <li style="top:46px">
      <svg width="9" height="9" viewBox="0 0 10 10"><path d="M2 0 L4 2.5 L3 4 C3.8 5.6 4.6 6.4 6 7 L7.5 6 L10 8 L8.5 10 C4 9.5 0.5 6 0 1.5 Z" fill="#111"/></svg>
      <div>Phone:&nbsp; 0203 555 0186</div>
    </li>
    <li style="top:72px">
      <svg width="9" height="9" viewBox="0 0 10 10"><circle cx="5" cy="5" r="4" fill="none" stroke="#111" stroke-width="1.6"/><path d="M5 2.5 V5 H7" fill="none" stroke="#111" stroke-width="1.2"/></svg>
      <div>Opening Times: 9am – 5pm Mon-Fri</div>
    </li>
    <li style="top:99px">
      <svg width="10" height="8" viewBox="0 0 10 8"><rect x="0" y="0" width="10" height="8" fill="#111"/><path d="M0 0 L5 4.5 L10 0" fill="none" stroke="#fff" stroke-width="1"/></svg>
      <div>Email: enquiry@brelwincare.co.uk</div>
    </li>
  </ul>

  <div class="social" aria-label="Social media links">
    <span style="background:#3b5998"></span>
    <span style="background:#4da7de"></span>
    <span style="background:#c2367f"></span>
    <span style="background:#0a66a8"></span>
  </div>

  <div class="map" role="img" aria-label="Street map showing the clinic location"></div>

  <footer class="site-footer">
    <p>Copyright © 2018. All rights reserved</p>
  </footer>
</body>
</html>
```